Website for International Non-Profit for Birth Parent Searching

LumaKin is a 501(c)(3) non-profit organization that helps Chinese adoptees search and reunite with birth families who were separated due the One Child Policy in China. We want to create a website that can link to an information database that allows website users to easily access information around search ads in an organized way; help connect families to professional searchers; provide resources for community support for adoptees and their families as they embark on a personal and emotional journey of finding birth family through support groups on social media and consultation/education on the searching process; and provide the opportunity for the adoptive community to give back through donations and volunteer opportunities. The final design should foster a sense of community and be easy navigable to access the multiple resources we provide to help families search for each other. We would like to see designs with red/black/white color schemes that are gentle, inviting, and family friendly to viewers. We would like to see some design layouts with Chinese themes, if possible.

```html
<!DOCTYPE html>
<html lang="en">
<head>
<meta charset="utf-8">
<title>LumaKin – Get Involved</title>
<link rel="stylesheet" href="https://fonts.googleapis.com/css2?family=Lato:wght@400;700;900&family=IBM+Plex+Sans:wght@600;700&family=Roboto:wght@400;500;700&display=swap">
<style>
:root{
  --red:#9b0010;
  --red-bright:#c8101e;
  --ink:#111;
  --text:#444;
  --blush:#f5e0e0;
  --white:#fff;
  --black:#0b0b0b;
  --muted:#ddd;
}
*{margin:0;padding:0;box-sizing:border-box}
html,body{width:1200px;height:2562px;overflow:hidden;background:var(--white)}
body{position:relative;font-family:"Lato",sans-serif;color:var(--ink)}
.abs{position:absolute}

/* header */
.site-header{left:0;top:0;width:1200px;height:90px;background:var(--white)}
.main-nav{left:305px;top:33px;display:flex;align-items:center;font-weight:700;font-size:14.5px;letter-spacing:-.3px;white-space:nowrap}
.main-nav span{margin-right:28px;display:flex;align-items:center;gap:10px}
.main-nav span:last-child{margin-right:0}
.main-nav .current{color:var(--red-bright)}
.donate-btn{left:930px;top:20px;width:150px;height:42px;background:var(--red);color:var(--white);font-weight:700;font-size:14px;display:flex;align-items:center;justify-content:center;border-radius:2px}
.lang{left:1100px;top:33px;font-weight:700;font-size:15px;display:flex;align-items:center;gap:10px}
.chev{width:10px;height:6px}

/* hero */
.hero{left:0;top:90px;width:1200px;height:390px}
.hero-photo{left:0;top:90px;width:1200px;height:390px;background:linear-gradient(100deg,#2f5d4f 0%,#b9b2a4 30%,#e6e1d8 55%,#6e625a 85%,#3d3330 100%)}
.brand-badge{left:63px;top:-12px;width:184px;height:184px;border-radius:50%;background:var(--white);display:flex;align-items:center;justify-content:center;padding-top:30px}
.brand-name{font-family:"Lato",sans-serif;font-weight:900;font-size:30px;color:var(--red-bright)}

/* intro */
.section-title{left:0;width:1200px;text-align:center;font-weight:900;font-size:34px;letter-spacing:-.5px}
.intro-title{top:540px}
.intro-text{left:175px;top:600px;width:850px;text-align:center;font-size:16.9px;line-height:24.2px;color:var(--text)}

/* cards */
.card{width:441px;height:350px;box-shadow:0 2px 6px rgba(0,0,0,.15)}
.card-photo{width:441px;height:272px}
.card-label{width:441px;height:78px;background:var(--red);color:var(--white);font-family:"IBM Plex Sans",sans-serif;font-weight:700;font-size:19px;letter-spacing:.6px;display:flex;align-items:center;justify-content:center}

/* contact */
.contact{left:0;top:1636px;width:1200px;height:626px;background:var(--blush)}
.contact-title{top:1717px}
.contact-title em{font-style:normal;color:var(--red-bright)}
.title-rule{left:566px;top:1771px;width:75px;height:3px;background:var(--red-bright)}
.field{background:var(--white);border:1px solid #cfc3c3;box-shadow:0 1px 3px rgba(0,0,0,.12);font-family:"Roboto",sans-serif;font-size:12px;color:#333;padding:16px 18px}
.submit-btn{left:526px;top:2143px;width:154px;height:39px;border-radius:20px;background:var(--red);color:var(--white);font-family:"Roboto",sans-serif;font-weight:500;font-size:14px;display:flex;align-items:center;justify-content:center}

/* footer */
.site-footer{left:0;top:2262px;width:1200px;height:300px;background:var(--black)}
.footer-brand{left:160px;top:2420px;width:144px;text-align:center;font-weight:900;font-size:36px;color:var(--white)}
.footer-nav{left:366px;top:2333px;display:flex;gap:27px;font-family:"Roboto",sans-serif;font-weight:500;font-size:13px;color:var(--white);white-space:nowrap}
.footer-rule{left:366px;top:2372px;width:682px;height:1px;background:#888}
.contact-item{top:2398px;display:flex;gap:16px;font-family:"Roboto",sans-serif;font-size:14px;line-height:19px;color:var(--white)}
.icon-box{width:30px;height:30px;background:var(--white);display:flex;align-items:center;justify-content:center;flex:none;margin-top:4px}
.copyright{left:366px;top:2469px;font-family:"Roboto",sans-serif;font-size:11px;color:var(--muted)}
</style>
</head>
<body>

<header class="abs site-header"></header>

<div class="abs hero-photo" role="img" aria-label="Photo of a young woman smiling at a laptop in a sunny home office"></div>
<svg class="abs hero" viewBox="0 0 1200 390" aria-hidden="true">
  <path d="M0,372 C250,300 500,320 650,355 C800,390 1000,380 1200,290 L1200,390 L0,390 Z" fill="#fff"/>
  <path d="M0,358 C250,286 500,306 650,341 C800,376 1000,366 1200,276 L1200,290 C1000,380 800,390 650,355 C500,320 250,300 0,372 Z" fill="#9b0010"/>
</svg>

<div class="abs brand-badge"><span class="brand-name">LumaKin</span></div>

<nav class="abs main-nav">
  <span>HOME</span>
  <span>WHO WE ARE <svg class="chev" viewBox="0 0 10 6"><path d="M1 1l4 4 4-4" stroke="#111" stroke-width="1.6" fill="none"/></svg></span>
  <span>START YOUR SEARCH</span>
  <span class="current">GET INVOLVED</span>
  <span>RESOURCES</span>
</nav>
<div class="abs donate-btn">DONATE NOW</div>
<div class="abs lang">EN <svg class="chev" viewBox="0 0 10 6"><path d="M1 1l4 4 4-4" stroke="#111" stroke-width="1.6" fill="none"/></svg></div>

<h1 class="abs section-title intro-title">GET INVOLVED</h1>
<p class="abs intro-text">Sed ut perspiciatis unde omnis iste natus error sit voluptatem accusantium doloremque laudantium, totam rem aperiam, eaque ipsa quae ab illo inventore veritatis et quasi architecto beatae vitae dicta sunt explicabo. Nemo enim ipsam voluptatem quia voluptas sit aspernatur aut odit aut fugit, sed quia consequuntur magni dolores eos qui ratione voluptatem sequi nesciunt. Neque porro quisquam est, qui dolorem ipsum quia dolor sit amet, consectetur, adipisci velit, sed quia non numquam eius modi tempora incidunt ut labore et dolore magnam aliquam quaerat voluptatem. Ut enim ad minima veniam, quis nostrum exercitationem ullam</p>

<div class="abs card" style="left:149px;top:800px">
  <div class="card-photo" role="img" aria-label="Photo of a woman presenting to colleagues at laptops" style="background:linear-gradient(135deg,#e9e7e3,#b9b6b2 60%,#4a4e55)"></div>
  <div class="card-label">UPCOMING EVENTS</div>
</div>
<div class="abs card" style="left:620px;top:800px">
  <div class="card-photo" role="img" aria-label="Photo of a multigenerational family in red celebrating the new year" style="background:linear-gradient(135deg,#e8e3da,#a8483f 55%,#6b2a26)"></div>
  <div class="card-label">VOLUNTEER OPPORTUNITIES</div>
</div>
<div class="abs card" style="left:149px;top:1180px">
  <div class="card-photo" role="img" aria-label="Photo of a confident woman standing in a busy cafe" style="background:linear-gradient(135deg,#ddd6cc,#9d6a55 55%,#5a463c)"></div>
  <div class="card-label">COMMUNITY CONNECTION</div>
</div>
<div class="abs card" style="left:620px;top:1180px">
  <div class="card-photo" role="img" aria-label="Photo of a group of friends laughing around a globe" style="background:linear-gradient(135deg,#f3e6cf,#a08a3a 50%,#5a3a2a)"></div>
  <div class="card-label">NEWS</div>
</div>

<section class="abs contact"></section>
<h2 class="abs section-title contact-title">GET <em>IN TOUCH</em></h2>
<div class="abs title-rule"></div>

<div class="abs field" style="left:230px;top:1814px;width:368px;height:44px;padding-top:15px">First Name</div>
<div class="abs field" style="left:608px;top:1814px;width:369px;height:44px;padding-top:15px">Last Name</div>
<div class="abs field" style="left:230px;top:1870px;width:368px;height:44px;padding-top:15px">Email address</div>
<div class="abs field" style="left:608px;top:1870px;width:369px;height:44px;padding-top:15px">Address</div>
<div class="abs field" style="left:230px;top:1926px;width:747px;height:57px">Phone number</div>
<div class="abs field" style="left:230px;top:1998px;width:747px;height:114px">Reason for inquiry</div>
<div class="abs submit-btn">SUBMIT</div>

<footer class="abs site-footer"></footer>
<div class="abs footer-brand">LumaKin</div>
<nav class="abs footer-nav">
  <span>HOME</span><span>WHO WE ARE</span><span>OUR SERVICES</span><span>GET INVOLVED</span><span>TOOLS AND RESOURCES</span><span>CONTACT US</span>
</nav>
<div class="abs footer-rule"></div>

<div class="abs contact-item" style="left:366px">
  <span class="icon-box"><svg width="16" height="16" viewBox="0 0 24 24"><path fill="#9b0010" d="M6.6 10.8a15.1 15.1 0 006.6 6.6l2.2-2.2a1 1 0 011-.25 11.4 11.4 0 003.6.57 1 1 0 011 1V20a1 1 0 01-1 1A17 17 0 013 4a1 1 0 011-1h3.5a1 1 0 011 1c0 1.250.2 2.45.57 3.57a1 1 0 01-.25 1z"/></svg></span>
  <span>Phone:<br>555-014-2290</span>
</div>
<div class="abs contact-item" style="left:536px">
  <span class="icon-box"><svg width="14" height="18" viewBox="0 0 24 32"><path fill="#9b0010" d="M12 0A12 12 0 000 12c0 9 12 20 12 20s12-11 12-20A12 12 0 0012 0zm0 17a5 5 0 110-10 5 5 0 010 10z"/></svg></span>
  <span>4210 Willow Bend Lane,<br>Suite 3B, Brookfield, CO 80099</span>
</div>
<div class="abs contact-item" style="left:788px">
  <span class="icon-box"><svg width="18" height="14" viewBox="0 0 24 18"><path fill="#9b0010" d="M0 0h24v18H0z"/><path d="M1 1l11 9 11-9" stroke="#fff" stroke-width="2" fill="none"/></svg></span>
  <span>Email:<br>hello@lumakin.org</span>
</div>

<div class="abs copyright">© COPYRIGHTS 2021 LUMAKIN &nbsp;| &nbsp; ALL RIGHTS RESERVED</div>

</body>
</html>
```